Personal Injury Lawyer Billboard

I would like a design created featuring the image of the lawyer centered in the middle of the design.
To the left of the lawyer's image it should read "INJURED?"
To the right of the lawyer's image, it should read "CALL DEAN!"
Under Call Dean, include the phone number 318-555-0187.
At the bottom of the design include the lawyers information "Dean Marlowe Accident & Injury Lawyers"
PLEASE REMOVED THE BACKGROUND IMAGERY OF THE PHOTO SUBMITTED. Also, the colors for this design should match the colors shown in the logo (navy, white and relective soft gold). Please use those color combinations in ways that best stand out.

```html
<!DOCTYPE html>
<html lang="en">
<head>
<meta charset="utf-8">
<title>Dean Marlowe Accident &amp; Injury Lawyers – Billboard</title>
<link rel="stylesheet" href="https://fonts.googleapis.com/css2?family=Cinzel:wght@500;600&family=Playfair+Display:wght@700;800&family=Libre+Caslon+Text:wght@400;700&display=swap">
<style>
  :root {
    --navy: #071a45;
    --navy-deep: #051335;
    --gold: #c69a32;
    --gold-soft: #d6ad4a;
    --white: #ffffff;
    --stage: #e8ecf2;
    --photo-top: #2a3a66;
    --photo-bottom: #17254d;
  }
  * { margin: 0; padding: 0; box-sizing: border-box; }
  html, body {
    width: 1200px;
    height: 1047px;
    overflow: hidden;
    background: var(--stage);
  }
  .canvas {
    position: relative;
    width: 1200px;
    height: 1047px;
  }
  .billboard {
    position: absolute;
    left: 40px;
    top: 358px;
    width: 1120px;
    height: 330px;
    background: linear-gradient(180deg, var(--navy-deep) 0%, var(--navy) 100%);
    overflow: hidden;
  }
  .headline {
    position: absolute;
    left: 34px;
    top: 58px;
    font-family: "Cinzel", serif;
    font-weight: 500;
    font-size: 66px;
    letter-spacing: 9px;
    color: var(--gold);
    line-height: 1;
  }
  .firm {
    position: absolute;
    left: 34px;
    top: 150px;
    width: 410px;
  }
  .firm-name {
    font-family: "Playfair Display", serif;
    font-weight: 800;
    font-size: 50px;
    letter-spacing: -1px;
    color: var(--white);
    line-height: 1;
    white-space: nowrap;
  }
  .firm-rule {
    height: 2px;
    background: var(--gold);
    margin: 8px 0 6px;
  }
  .firm-tagline {
    font-family: "Libre Caslon Text", serif;
    font-weight: 400;
    font-size: 25px;
    color: var(--white);
    letter-spacing: 0.5px;
    white-space: nowrap;
    line-height: 1.1;
  }
  .lawyer-photo {
    position: absolute;
    left: 466px;
    top: 26px;
    width: 310px;
    height: 304px;
    background: linear-gradient(180deg, var(--photo-top) 0%, var(--photo-bottom) 100%);
    border-radius: 140px 140px 0 0;
  }
  .call {
    position: absolute;
    left: 812px;
    top: 150px;
  }
  .call-title {
    font-family: "Cinzel", serif;
    font-weight: 600;
    font-size: 44px;
    letter-spacing: 3px;
    color: var(--gold);
    line-height: 1;
    white-space: nowrap;
  }
  .call-phone {
    display: flex;
    align-items: center;
    gap: 12px;
    margin-top: 18px;
  }
  .call-icon { width: 36px; height: 36px; flex: none; }
  .call-number {
    font-family: "Cinzel", serif;
    font-weight: 500;
    font-size: 36px;
    letter-spacing: 1px;
    color: var(--gold);
    line-height: 1;
    white-space: nowrap;
  }
</style>
</head>
<body>
  <main class="canvas">
    <section class="billboard">
      <h1 class="headline">INJURED</h1>

      <div class="firm">
        <p class="firm-name">DEAN MARLOWE</p>
        <div class="firm-rule"></div>
        <p class="firm-tagline">ACCIDENT &amp; INJURY LAWYERS</p>
        <div class="firm-rule"></div>
      </div>

      <div class="lawyer-photo" role="img" aria-label="Portrait of the lawyer in a navy suit and green tie, raising a fist, background removed"></div>

      <div class="call">
        <p class="call-title">CALL DEAN</p>
        <div class="call-phone">
          <svg class="call-icon" viewBox="0 0 36 36" aria-hidden="true">
            <circle cx="18" cy="18" r="16" fill="none" stroke="var(--gold)" stroke-width="2.5"/>
            <path d="M12.5 10.5l3 -0.5 1.6 4 -2 1.6c0.9 2.2 2.6 3.9 4.8 4.8l1.6 -2 4 1.6 -0.5 3c-0.2 1 -1 1.6 -2 1.5 -6.2 -0.5 -11.1 -5.4 -11.6 -11.6 -0.1 -1 0.5 -1.8 1.1 -2.4z" fill="var(--gold)"/>
          </svg>
          <span class="call-number">318-555-0187</span>
        </div>
      </div>
    </section>
  </main>
</body>
</html>
```